Advertising company unique advertising platform

we need a logo design for a new company based in Australia Melbourne. We develop innovated advertising platform where consumer can use this platform to get regular discount, as business owner they can use this platform for free advertisement. Payment for this advertisement platform only payable every two weeks, when I generate revenue for their business

Industry/Entity Type

Advertising

Contact Information for Business Card

Dale Morven | Co-Founder |Managing Director
Suite 718 240 Wattlebrook Lane Melbourne Vic 3000

ABN 38 614 207 923
Tel: +61 0487 259 318 | Email: dale.morven@plivorantu.com

Font styles to use
Decorative
Script

Requirements
Must have
• Try few different design and some round corner business card
Should not have
• One round corner business card...try 4 different colour background not only black, make sure two side is designed. Be creative so imagine you are giving this to a client make sure has wow factor, if you can also try one design with engrave like all the logo, words look 3d feel
• The word Advertising Platform use attached file font

```html
<!DOCTYPE html>
<html lang="en">
<head>
<meta charset="utf-8">
<title>Tellomar Hub – Business Card</title>
<link rel="stylesheet" href="https://fonts.googleapis.com/css2?family=Source+Sans+3:wght@400;600;700&display=swap">
<style>
  :root {
    --stage: #3b322e;
    --card: #151515;
    --card-edge: #222;
    --ink: #f2f2f2;
    --muted: #8f8f8f;
    --accent-red: #e2452c;
    --accent-teal: #3fe0b5;
    --brand: #f08a3a;
    --divider: #5a5a5a;
  }
  * { margin: 0; padding: 0; box-sizing: border-box; }
  html, body {
    width: 1200px; height: 864px; overflow: hidden;
    background: var(--stage);
    font-family: "Source Sans 3", "Myriad Pro", Arial, sans-serif;
  }
  .sheet {
    width: 1200px; height: 864px;
    display: flex; flex-direction: column;
    align-items: center; justify-content: center; gap: 48px;
  }
  .card {
    width: 630px; height: 360px;
    background: var(--card);
    border: 1px solid var(--card-edge);
    position: relative;
    box-shadow: 0 10px 30px rgba(0,0,0,.45);
  }
  /* brand mark stand-in */
  .brand { display: flex; align-items: center; gap: 10px; }
  .brand-dot { width: 18px; height: 18px; border-radius: 50%; background: var(--brand); }
  .brand-name { color: var(--brand); font-weight: 600; font-size: 30px; letter-spacing: .5px; white-space: nowrap; }

  /* back side */
  .card-back .brand { position: absolute; left: 200px; top: 130px; }
  .card-back .website {
    position: absolute; left: 190px; top: 240px;
    color: var(--muted); font-size: 14px; letter-spacing: 5px;
  }

  /* front side */
  .card-front .brand { position: absolute; left: 38px; top: 158px; }
  .card-front .divider {
    position: absolute; left: 298px; top: 60px; width: 1px; height: 240px;
    background: linear-gradient(to bottom, transparent, var(--divider) 20%, var(--divider) 80%, transparent);
  }
  .contact { position: absolute; left: 326px; top: 62px; color: var(--ink); font-size: 17px; line-height: 1.28; }
  .contact .name { color: var(--accent-red); font-weight: 700; font-size: 18px; text-transform: uppercase; }
  .contact .role { color: var(--accent-teal); font-size: 18px; text-transform: uppercase; }
  .contact .company { margin-top: 4px; }
  .contact .line { display: flex; align-items: center; gap: 8px; }
  .contact .icon { width: 13px; height: 13px; fill: var(--accent-red); flex: none; }
</style>
</head>
<body>
<main class="sheet">
  <section class="card card-back" aria-label="Card back">
    <div class="brand"><span class="brand-dot"></span><span class="brand-name">Tellomar Hub</span></div>
    <p class="website">www.plivorantu.com</p>
  </section>

  <section class="card card-front" aria-label="Card front">
    <div class="brand"><span class="brand-dot"></span><span class="brand-name">Tellomar Hub</span></div>
    <div class="divider"></div>
    <div class="contact">
      <p class="name">Dale Morven</p>
      <p class="role">Co-Founder</p>
      <p class="role">Managing Director</p>
      <p class="company">Plivorantu</p>
      <p>ABN 38 614 207 923</p>
      <p>Suite 718 240 Wattlebrook Lane</p>
      <p>Melbourne Vic 3000</p>
      <p class="line">
        <svg class="icon" viewBox="0 0 16 16" aria-hidden="true"><path d="M3 1h3l1.5 4-2 1.3a9 9 0 0 0 4.2 4.2L11 8.5 15 10v3a2 2 0 0 1-2 2A12 12 0 0 1 1 3a2 2 0 0 1 2-2z"/></svg>
        +61 0487 259 318
      </p>
      <p class="line">
        <svg class="icon" viewBox="0 0 16 16" aria-hidden="true"><path d="M1 3h14v10H1z" opacity=".9"/><path d="M1 3l7 6 7-6" fill="none" stroke="#151515" stroke-width="1.4"/></svg>
        dale.morven@plivorantu.com
      </p>
    </div>
  </section>
</main>
</body>
</html>
```